Varnik Holdings — Business Card Design Brief
Overview
Design a double-sided business card for Varnik Holdings that highlights our two service arms: Varnik Communications (telecommunications) and Varnik Energy (business energy solutions). The card should feel smart and stand out when handed to clients.

Objectives
Showcase our areas of specialty clearly.
Reflect the overall Varnik / Varnik Holdings brand while acknowledging both arms.
Explore using both logos (Communications + Energy) or one unified logo, depending on the design.

Deliverables
One double-sided business card design (front + back).

Content & Copy
Front (preferred): Logo: Varnik / Varnik Holdings
Descriptor: Business Communications | Business Energy
Back:My contact details and company details
Core products: Business Mobile • Telephony • Internet • Business Energy Solutions

Brand & Visual Direction
We have a group logo currently tailored more toward telecoms, plus a separate Varnik Energy logo.
Please explore layouts that use both logos or just one, whichever works best.
Color: I wouldn't mind seeing an option using our the Blue/Purple gradient from our website (varnik-example.co.uk), but also open to non-gradient approaches and other colours..

Overall look: Smart, modern, and distinctive.
Format & Print Specs
Double-sided business card format. (Use a standard size

Must-Haves
Front: Varnik wording or Varnik Holdings wording with atleast 1 logo also on front “Business Communications | Business Energy.”

Back: Contact + company details and core products.
A design that stands out while remaining professional.

Nice-to-Have Options
A gradient version using our site’s Blue/Purple gradient.
A non-gradient version.
A dual-logo treatment versus a single-logo treatment.

Thanks
Owen

```html
<!DOCTYPE html>
<html lang="en">
<head>
<meta charset="utf-8">
<title>Varnik Holdings — Business Card</title>
<link href="https://fonts.googleapis.com/css2?family=Montserrat:wght@400;500;800&display=swap" rel="stylesheet">
<style>
  :root {
    --stage: #3a3a3c;
    --navy: #252466;
    --blue: #2f6bbf;
    --sky: #29a8e0;
    --lime: #c9d92b;
    --green: #5cb848;
    --white: #ffffff;
  }
  * { box-sizing: border-box; margin: 0; padding: 0; }
  html, body {
    width: 1200px; height: 875px; overflow: hidden;
    background: var(--stage);
    font-family: "Montserrat", Arial, sans-serif;
  }
  .stage { width: 1200px; height: 875px; position: relative; }
  .card {
    position: absolute; width: 620px; height: 354px;
    border-radius: 18px; overflow: hidden;
    box-shadow: 0 14px 30px rgba(0,0,0,.35);
  }
  /* Front */
  .card-front { left: 60px; top: 50px; background: var(--navy); }
  .front-brands {
    position: absolute; left: 0; right: 0; top: 118px;
    display: flex; justify-content: center; align-items: center; gap: 28px;
  }
  .brand {
    display: flex; align-items: center; gap: 10px;
    font-weight: 800; font-size: 20px; white-space: nowrap;
  }
  .brand-dot { flex: none; width: 30px; height: 30px; border-radius: 50%; }
  .brand-comms { color: var(--sky); }
  .brand-comms .brand-dot { background: var(--blue); }
  .brand-energy { color: var(--green); }
  .brand-energy .brand-dot { background: var(--green); }
  .front-divider { width: 1px; height: 70px; background: var(--lime); opacity: .8; }
  .descriptor {
    position: absolute; left: 0; right: 0; bottom: 88px; text-align: center;
    font-size: 17px; font-weight: 500; letter-spacing: .3px; white-space: nowrap;
  }
  .descriptor .comms { color: var(--sky); }
  .descriptor .sep { color: var(--white); margin: 0 6px; }
  .descriptor .energy { color: var(--lime); }

  /* Back */
  .card-back { left: 520px; top: 470px; background: var(--white); }
  .back-wave { position: absolute; inset: 0; }
  .back-brands { position: absolute; left: 34px; top: 78px; display: flex; gap: 36px; }
  .back-brand {
    display: flex; align-items: center; gap: 8px;
    color: var(--navy); font-weight: 800; font-size: 24px; white-space: nowrap;
  }
  .back-brand .brand-dot { width: 22px; height: 22px; }
  .back-brand.comms .brand-dot { background: var(--blue); }
  .back-brand.energy .brand-dot { background: var(--green); }
  .holder { position: absolute; right: 30px; top: 24px; text-align: right; color: var(--navy); }
  .holder-name { font-weight: 800; font-size: 21px; letter-spacing: .5px; white-space: nowrap; }
  .holder-role { font-size: 12px; margin-top: 2px; }
  .contact {
    position: absolute; right: 30px; top: 150px; text-align: right;
    color: var(--white); font-size: 12.5px; line-height: 1.65; white-space: nowrap;
  }
  .contact-line { display: flex; justify-content: flex-end; align-items: center; gap: 7px; }
  .contact-icon { width: 11px; height: 11px; fill: var(--sky); }
  .products {
    position: absolute; left: 34px; bottom: 24px; color: var(--white);
    font-size: 12.5px; line-height: 1.7; white-space: nowrap;
  }
  .products span::before { content: "•"; color: var(--sky); margin-right: 4px; }
  .products span { margin-right: 10px; }
</style>
</head>
<body>
<main class="stage">

  <section class="card card-front" aria-label="Card front">
    <div class="front-brands">
      <div class="brand brand-comms"><span class="brand-dot"></span>Varnik Communications</div>
      <div class="front-divider"></div>
      <div class="brand brand-energy"><span class="brand-dot"></span>Varnik Energy</div>
    </div>
    <p class="descriptor">
      <span class="comms">Business Communications</span><span class="sep">|</span><span class="energy">Business Energy</span>
    </p>
  </section>

  <section class="card card-back" aria-label="Card back">
    <svg class="back-wave" viewBox="0 0 620 354" preserveAspectRatio="none" aria-hidden="true">
      <path d="M0,240 C150,268 260,236 335,160 C395,100 460,84 620,80 L620,94 C480,98 420,110 365,168 C295,245 175,285 0,254 Z" fill="#2f6bbf"/>
      <path d="M0,262 C170,292 290,250 360,175 C420,112 480,104 620,100 L620,354 L0,354 Z" fill="#252466"/>
      <path d="M60,276 C200,296 300,256 368,182 C425,122 480,110 570,106" fill="none" stroke="#ffffff" stroke-width="3"/>
    </svg>

    <div class="back-brands">
      <div class="back-brand comms"><span class="brand-dot"></span>Varnik</div>
      <div class="back-brand energy"><span class="brand-dot"></span>Varnik</div>
    </div>

    <div class="holder">
      <p class="holder-name">DORIAN PELL</p>
      <p class="holder-role">Founder/CEO</p>
    </div>

    <div class="contact">
      <p class="contact-line">24 Kestrel Row</p>
      <p class="contact-line">Leeds England, LS2 7QT</p>
      <p class="contact-line">+44 0113 496 0721
        <svg class="contact-icon" viewBox="0 0 24 24" aria-hidden="true"><path d="M6.6 10.8a15 15 0 0 0 6.6 6.6l2.2-2.2c.3-.3.7-.4 1-.2 1.1.4 2.3.6 3.6.6.6 0 1 .4 1 1V20c0 .6-.4 1-1 1A17 17 0 0 1 3 4c0-.6.4-1 1-1h3.5c.6 0 1 .4 1 1 0 1.3.2 2.5.6 3.6.1.3 0 .7-.2 1z"/></svg></p>
      <p class="contact-line">info@varnik-example.co.uk
        <svg class="contact-icon" viewBox="0 0 24 24" aria-hidden="true"><path d="M2 5h20v14H2z M2 5l10 8 10-8"/></svg></p>
      <p class="contact-line">www.varnik-example.co.uk
        <svg class="contact-icon" viewBox="0 0 24 24" aria-hidden="true"><circle cx="12" cy="12" r="10"/></svg></p>
    </div>

    <p class="products">
      <span>Business Mobile</span><span>Internet</span><br>
      <span>Telephony</span><span>Business Energy Solutions</span>
    </p>
  </section>

</main>
</body>
</html>
```